Bork Ventures, Inc. Website redesign

Revamp the website, it is old and outdated. www.borkventuresinc.example

Target Market(s)

Information Technology Consulting and Staffing

Coding

Coded - Design and coding required

Number of Pages Required

5+ page

Colors

Designer to choose colors to be used in the design.

Requirements
Must have
• Outlined text boxes just like from the Tolvane.example site. A clean look

```html
<!DOCTYPE html>
<html lang="en">
<head>
<meta charset="utf-8">
<title>Bork Ventures, Inc. — IT Consulting</title>
<link href="https://fonts.googleapis.com/css2?family=Lexend:wght@400;500;600&family=Mulish:wght@400;600;700&display=swap" rel="stylesheet">
<style>
:root{
  --red:#9b1b30;
  --red-dark:#7f1427;
  --ink:#1d1d1f;
  --text:#6b6b6b;
  --light:#f1f1f1;
  --white:#ffffff;
  --hero-a:#1c2230;
  --hero-b:#0d1118;
}
*{box-sizing:border-box;margin:0;padding:0}
html,body{width:1200px;height:4047px;overflow:hidden}
body{position:relative;font-family:"Mulish",sans-serif;color:var(--text);background:var(--white)}
section,header,footer{position:absolute;left:0;width:1200px}
.abs{position:absolute}
h1,h2,h3{font-family:"Lexend",sans-serif;color:var(--ink);font-weight:500}
.center{left:0;width:1200px;text-align:center}
.bar{position:absolute;width:40px;height:3px;background:var(--red)}
.bar.mid{left:580px}
.btn{position:absolute;display:flex;align-items:center;justify-content:center;font-family:"Lexend",sans-serif;font-size:18px;color:var(--white);text-decoration:none}
.btn.solid{background:var(--red)}
.btn.outline{border:2px solid var(--white)}

/* header */
.site-header{top:0;height:83px;background:var(--white)}
.brand{position:absolute;left:77px;top:26px;font-family:"Lexend",sans-serif;font-weight:400;font-size:25px;color:var(--ink);display:flex;align-items:center;gap:10px;white-space:nowrap}
.brand .mark{width:14px;height:14px;background:var(--red)}
.nav{position:absolute;top:36px;font-family:"Lexend",sans-serif;font-size:13px;color:var(--ink);letter-spacing:.3px}
.nav.active{color:var(--red)}
.phone{position:absolute;left:955px;top:26px;display:flex;align-items:center;gap:8px;font-family:"Lexend",sans-serif;font-size:20px;font-weight:500;color:var(--red)}
.phone .dot{width:33px;height:33px;border-radius:50%;background:var(--red);display:flex;align-items:center;justify-content:center}

/* hero */
.hero{top:83px;height:594px;background:linear-gradient(100deg,#2b2f3a 0%,var(--hero-a) 35%,var(--hero-b) 100%)}
.hero h1{position:absolute;right:80px;text-align:right;color:var(--white);font-weight:600;font-size:53px;line-height:60px;top:170px}
.hero p{position:absolute;right:80px;top:303px;text-align:right;color:#e8e8e8;font-size:17px;line-height:27px}
.arrow{position:absolute;top:261px;width:50px;height:50px;border:1.5px solid rgba(255,255,255,.6);border-radius:50%}

/* services */
.services{top:677px;height:572px;background:var(--light)}
.section-title{position:absolute;font-size:42px;font-weight:500}
.section-sub{position:absolute;font-size:15px;color:#444}
.card{position:absolute;background:var(--white)}
.service-card{top:198px;width:273px;height:311px}
.card h3{position:absolute;left:24px;font-size:20px;line-height:26px;font-weight:500}
.card p{position:absolute;left:24px;right:22px;font-size:13px;line-height:26px;color:#888}
.read{position:absolute;font-family:"Lexend",sans-serif;font-size:13px;color:var(--red);display:flex;align-items:center;gap:8px}
.read::after{content:"";border-left:6px solid var(--red);border-top:4px solid transparent;border-bottom:4px solid transparent}
.icon{position:absolute;left:24px;top:30px}

/* welcome */
.welcome{top:1249px;height:600px;background:var(--white)}
.eyebrow{position:absolute;left:99px;top:64px;font-size:15px;color:var(--red);letter-spacing:1px}
.welcome h2{position:absolute;left:94px;top:96px;font-size:38px;line-height:50px}
.welcome p{position:absolute;left:99px;width:486px;font-size:13.5px;line-height:27px;color:#777}
.welcome p a{color:var(--red);text-decoration:none;font-weight:600}
.photo{position:absolute;left:685px;top:67px;width:416px;height:468px;border-radius:4px;background:linear-gradient(160deg,#6d6b68 0%,#3f3d3b 55%,#262422 100%)}

/* band */
.band{top:1849px;height:290px;background:linear-gradient(90deg,var(--red-dark),var(--red) 50%,var(--red-dark))}
.band p{position:absolute;top:70px;font-family:"Lexend",sans-serif;font-size:27px;line-height:41px;color:var(--white);font-weight:400}

/* strategy */
.strategy{top:2139px;height:614px;background:var(--light)}
.strategy-card{top:194px;width:364px;height:312px}
.dots{position:absolute;top:0;left:580px;display:flex;gap:6px}
.dots span{width:14px;height:14px;border-radius:50%;border:1.5px solid var(--red)}
.dots span.on{background:var(--red)}

/* news */
.news{top:2753px;height:605px;background:var(--white)}
.news-card{position:absolute;top:187px;width:364px;height:311px;border-radius:3px;overflow:hidden}
.news-card .shade{position:absolute;inset:0;background:linear-gradient(180deg,rgba(0,0,0,0) 45%,rgba(0,0,0,.75) 100%)}
.news-card .date{position:absolute;left:25px;top:210px;font-size:13px;color:var(--red)}
.news-card .title{position:absolute;left:25px;top:239px;width:300px;font-size:14.5px;line-height:27px;color:var(--white)}

/* contact */
.contact{top:3358px;height:522px;background:linear-gradient(90deg,var(--red-dark),var(--red) 60%,#8c1729)}
.contact h2{position:absolute;left:79px;top:54px;font-size:40px;color:var(--white)}
.contact .lead{position:absolute;left:79px;top:104px;font-size:15px;line-height:27px;color:#f3dfe2}
.contact .bar{left:79px;top:181px;background:var(--white)}
.contact-box{position:absolute;left:79px;top:217px;width:606px;height:228px;background:var(--white)}
.map{position:absolute;left:0;top:0;width:306px;height:228px;background:linear-gradient(135deg,#eef0ec,#dfe4dc)}
.address h3{position:absolute;left:345px;top:32px;font-size:19px;color:var(--red)}
.address .lines{position:absolute;left:378px;top:78px;font-size:13px;line-height:27px;color:#666}
.address .tel{position:absolute;left:378px;top:165px;font-family:"Lexend",sans-serif;font-size:18px;color:var(--red)}

/* footer */
.site-footer{top:3880px;height:167px;background:var(--white)}
.site-footer .brand{left:77px;top:38px}
.flink{position:absolute;font-size:13px;color:#444}
.social{position:absolute;top:18px;width:42px;height:42px;border-radius:50%}
.copy{position:absolute;left:782px;top:94px;font-size:12.5px;color:#444}
</style>
</head>
<body>

<header class="site-header">
  <div class="brand"><span>Bork Ventures</span><span class="mark"></span></div>
  <svg class="abs" style="left:371px;top:38px" width="13" height="11" viewBox="0 0 13 11"><path d="M6.5 10 1 4.5 3 1h7l2 3.5z" fill="#9b1b30"/></svg>
  <span class="nav active" style="left:391px">HOME</span>
  <span class="nav" style="left:460px">ABOUT US</span>
  <span class="nav" style="left:558px">SERVICES</span>
  <span class="nav" style="left:653px">STRATEGY</span>
  <span class="nav" style="left:752px">IT NEWS</span>
  <span class="nav" style="left:836px">CONTACT US</span>
  <div class="phone"><span class="dot"><svg width="16" height="16" viewBox="0 0 24 24"><path d="M6.6 10.8a15 15 0 0 0 6.6 6.6l2.2-2.2a1 1 0 0 1 1-.25 11 11 0 0 0 3.6.6 1 1 0 0 1 1 1V20a1 1 0 0 1-1 1A17 17 0 0 1 3 4a1 1 0 0 1 1-1h3.5a1 1 0 0 1 1 1c0 1.25.2 2.45.6 3.6a1 1 0 0 1-.25 1z" fill="#fff"/></svg></span>301-555-0148</div>
</header>

<section class="hero" role="img" aria-label="Photo of a woman touching a glowing circuit-board display at night">
  <div class="arrow" style="left:16px"><svg width="50" height="50" viewBox="0 0 50 50"><path d="M28 17 20 25l8 8" stroke="#fff" stroke-width="1.5" fill="none"/></svg></div>
  <div class="arrow" style="left:1136px"><svg width="50" height="50" viewBox="0 0 50 50"><path d="M22 17l8 8-8 8" stroke="#fff" stroke-width="1.5" fill="none"/></svg></div>
  <h1>OUR MISSION<br>INTEGRITY RESULTS</h1>
  <p>Bork Ventures, Inc. is an 8(a) innovative and rapidly<br>growing full-service IT consulting firm</p>
  <a class="btn solid" style="left:768px;top:374px;width:170px;height:55px">CONTACT US</a>
  <a class="btn outline solid" style="left:950px;top:374px;width:170px;height:55px">LEARN MORE</a>
</section>

<section class="services">
  <h2 class="section-title center" style="top:54px">Services We Provide You</h2>
  <p class="section-sub center" style="top:113px">Our people and our process is what makes us successful in providing these services.</p>
  <div class="bar mid" style="top:147px"></div>

  <article class="card service-card" style="left:27px">
    <svg class="icon" width="64" height="62" viewBox="0 0 64 62" fill="none" stroke="#222" stroke-width="2"><rect x="18" y="10" width="40" height="28"/><path d="M30 38v8h16v-8M26 48h24"/><circle cx="38" cy="22" r="6" stroke="#9b1b30"/><rect x="4" y="30" width="14" height="22"/><circle cx="54" cy="54" r="5" stroke="#9b1b30"/></svg>
    <h3 style="top:125px">Hardware /<br>Software Sales</h3>
    <p style="top:186px">We have access to multiple distri - butor partners throughout North America, as well as Crestline.</p>
    <span class="read" style="right:22px;top:280px">Read More</span>
  </article>
  <article class="card service-card" style="left:319px">
    <svg class="icon" width="64" height="62" viewBox="0 0 64 62" fill="none" stroke="#222" stroke-width="2"><circle cx="32" cy="30" r="18"/><path d="M32 4v8M32 48v8M6 30h8M50 30h8M13 11l6 6M45 43l6 6M51 11l-6 6M19 43l-6 6"/><circle cx="32" cy="30" r="8" stroke="#9b1b30"/></svg>
    <h3 style="top:125px">Professional<br>Services</h3>
    <p style="top:186px">Our team provides experienced leadership and guidance, utilizing the industry standard.</p>
    <span class="read" style="right:22px;top:280px">Read More</span>
  </article>
  <article class="card service-card" style="left:609px">
    <svg class="icon" width="64" height="62" viewBox="0 0 64 62" fill="none" stroke="#222" stroke-width="2"><rect x="16" y="14" width="32" height="38" rx="3"/><path d="M22 14V6M30 14V6M38 14V6M46 14V6M16 24H8M16 34H8M16 44H8M48 24h8M48 34h8M48 44h8"/><path d="M24 42V30a8 8 0 0 1 16 0v12z" stroke="#9b1b30"/></svg>
    <h3 style="top:125px">Technology<br>Assessment</h3>
    <p style="top:186px">Experience has shown companies that perform objective, third-party technology assessments.</p>
    <span class="read" style="right:22px;top:280px">Read More</span>
  </article>
  <article class="card service-card" style="left:900px">
    <svg class="icon" width="66" height="62" viewBox="0 0 66 62" fill="none" stroke="#222" stroke-width="2"><rect x="4" y="12" width="50" height="34"/><path d="M22 46v8h14v-8M14 56h30M12 22h18M12 30h24M12 38h14"/><circle cx="56" cy="10" r="7" stroke="#9b1b30"/><path d="M36 22h12v12H36z" stroke="#9b1b30"/></svg>
    <h3 style="top:125px">Technology<br>Consulting</h3>
    <p style="top:186px">Implementing quality solutions is more than applying technology to problems. You need experts.</p>
    <span class="read" style="right:22px;top:280px">Read More</span>
  </article>
</section>

<section class="welcome">
  <span class="eyebrow">WELCOME TO</span>
  <h2>Bringing Thought Leadership<br>&amp; Quality to Every Project</h2>
  <div class="bar" style="left:99px;top:204px"></div>
  <p style="top:229px">Bork Ventures, Inc. is an 8(a) full-service IT consulting company based in the Washington, DC Metro area. We offer specialized, highly customized technology solutions for our customers located throughout the United States. <a>Learn about our Services now.</a></p>
  <p style="top:357px">No two businesses are the same. We believe the technology supporting your business operations should align with your company. Every project begins with a thorough analysis of your current technology environment. We work with you to define the environment you want.</p>
  <a class="btn solid" style="left:97px;top:480px;width:172px;height:55px">LEARN MORE</a>
  <div class="photo" role="img" aria-label="Photo of a technician working on a laptop beside a server rack"></div>
</section>

<section class="band">
  <p class="center">For over 20 + years, we have been providing reliable IT solutions to<br>businesses in the Washington, DC Metro area and beyond.</p>
  <a class="btn outline" style="left:514px;top:166px;width:171px;height:57px">CONTACT US</a>
</section>

<section class="strategy">
  <h2 class="section-title center" style="top:56px">Our Strategy</h2>
  <p class="section-sub center" style="top:115px">Your Path to Success</p>
  <div class="bar mid" style="top:152px"></div>

  <article class="card strategy-card" style="left:27px">
    <svg class="icon" width="64" height="66" viewBox="0 0 64 66" fill="none" stroke="#222" stroke-width="2"><path d="M14 60V46C6 40 4 30 8 20 14 6 36 2 46 14c6 8 6 18 2 24v22"/><circle cx="30" cy="28" r="10" stroke="#9b1b30"/><path d="M30 14v4M30 38v4M16 28h4M40 28h4"/></svg>
    <h3 style="top:125px">Assess</h3>
    <p style="top:162px">Our case-specific technology audit and data gathering provides us with a detailed and comprehensive picture of your.</p>
    <span class="read" style="left:24px;top:258px">Read More</span>
  </article>
  <article class="card strategy-card" style="left:418px">
    <svg class="icon" width="66" height="66" viewBox="0 0 66 66" fill="none" stroke="#222" stroke-width="2"><rect x="4" y="6" width="52" height="44"/><path d="M12 16h36M12 24h36M12 32h14"/><circle cx="50" cy="44" r="8" stroke="#9b1b30"/><path d="M46 52v10l4-3 4 3V52" stroke="#9b1b30"/></svg>
    <h3 style="top:125px">Recommend</h3>
    <p style="top:162px">Our research and analysis is summarized in a proposal for individually designed solutions that suit your business.</p>
    <span class="read" style="left:24px;top:258px">Read More</span>
  </article>
  <article class="card strategy-card" style="left:807px">
    <svg class="icon" width="66" height="66" viewBox="0 0 66 66" fill="none" stroke="#222" stroke-width="2"><circle cx="30" cy="32" r="13"/><circle cx="30" cy="32" r="5" stroke="#9b1b30"/><path d="M30 14v5M30 45v5M12 32h5M43 32h5"/><path d="M38 4h14l8 8M28 60H14l-8-8" stroke="#9b1b30"/></svg>
    <h3 style="top:125px">Implement</h3>
    <p style="top:162px">Bork Ventures, Inc. manages all aspects of the implementation process, including design, procu rement, project management.</p>
    <span class="read" style="left:24px;top:258px">Read More</span>
  </article>

  <div class="dots" style="top:545px"><span class="on"></span><span></span></div>
</section>

<section class="news">
  <h2 class="section-title center" style="top:58px">Latest News</h2>
  <p class="section-sub center" style="top:114px">Mission Integrity Results</p>
  <div class="bar mid" style="top:152px"></div>

  <article class="news-card" style="left:27px;background:linear-gradient(135deg,#5b6a5a,#2f3a45 60%,#8f7a68)" role="img" aria-label="Photo of two colleagues talking in an office">
    <div class="shade"></div><span class="date">05 Sep 2019</span><p class="title">Lorem ipsum Simple Text of print Type Text Type Industry !</p>
  </article>
  <article class="news-card" style="left:418px;background:linear-gradient(135deg,#3c4a4c,#242d35 60%,#4a5257)" role="img" aria-label="Photo of a smiling businessman in a meeting">
    <div class="shade"></div><span class="date">05 Sep 2019</span><p class="title">Lorem ipsum Simple Text of print Type Text Type Industry !</p>
  </article>
  <article class="news-card" style="left:807px;background:radial-gradient(circle at 45% 40%,#8fc6e0,#2f6d96 40%,#182636 75%)" role="img" aria-label="Illustration of a glowing globe">
    <div class="shade"></div><span class="date">05 Sep 2019</span><p class="title">Lorem ipsum Simple Text of print Type Text Type Industry !</p>
  </article>

  <div class="dots" style="top:532px"><span class="on"></span><span></span></div>
</section>

<section class="contact">
  <h2>Contact Us</h2>
  <p class="lead">Feel free to contact us in case you have any question or suggestion.<br>Use the below contact information</p>
  <div class="bar"></div>
  <div class="contact-box">
    <div class="map" role="img" aria-label="Street map showing the office location"></div>
    <div class="address">
      <h3>Address</h3>
      <svg class="abs" style="left:345px;top:82px" width="16" height="24" viewBox="0 0 16 24"><path d="M8 0a8 8 0 0 1 8 8c0 6-8 16-8 16S0 14 0 8a8 8 0 0 1 8-8z" fill="#9b1b30"/><circle cx="8" cy="8" r="3" fill="#fff"/></svg>
      <p class="lines">Bork Ventures, Inc.<br>2280 Hollowbrook Dr<br>Ashcombe, MD 20990</p>
      <svg class="abs" style="left:345px;top:168px" width="18" height="18" viewBox="0 0 24 24"><path d="M6.6 10.8a15 15 0 0 0 6.6 6.6l2.2-2.2a1 1 0 0 1 1-.25 11 11 0 0 0 3.6.6 1 1 0 0 1 1 1V20a1 1 0 0 1-1 1A17 17 0 0 1 3 4a1 1 0 0 1 1-1h3.5a1 1 0 0 1 1 1c0 1.25.2 2.45.6 3.6a1 1 0 0 1-.25 1z" fill="#9b1b30"/></svg>
      <span class="tel">301-555-0148</span>
    </div>
  </div>
</section>

<footer class="site-footer">
  <div class="brand"><span>Bork Ventures</span><span class="mark"></span></div>
  <span class="flink" style="left:405px;top:35px">Home</span>
  <span class="flink" style="left:405px;top:71px">About Us</span>
  <span class="flink" style="left:405px;top:107px">Services</span>
  <span class="flink" style="left:565px;top:35px">Strategy</span>
  <span class="flink" style="left:565px;top:71px">It News</span>
  <span class="flink" style="left:565px;top:107px">Contact Us</span>
  <span class="social" style="left:775px;background:#3b5b9a" role="img" aria-label="Social profile link"></span>
  <span class="social" style="left:822px;background:#1f77b4" role="img" aria-label="Social profile link"></span>
  <span class="copy">© Bork Ventures - 2019 All Rights reserved | Policy</span>
</footer>

</body>
</html>
```